The quiet harbor with an elephant incorporated in the background

Target Market(s)

Real estate

Industry/Entity Type

Real Estate

Contact Information for Business Card

On back on want my name & number
In front I want the business name, "the quiet harbor", below to say staging & design

Logo Text

The quiet harbor

Font styles to use
Serif

Colors
000000

Requirements
Must have
• I want an elephant behind the writing in gold transperant

```html
<!DOCTYPE html>
<html lang="en">
<head>
<meta charset="utf-8">
<title>The Quiet Harbor – Business Card</title>
<link rel="stylesheet" href="https://fonts.googleapis.com/css2?family=Cinzel:wght@400&family=Open+Sans:wght@400;700&family=Quicksand:wght@400&display=swap">
<style>
  :root {
    --backdrop-top: #c9c9c9;
    --backdrop-bottom: #fbfbfb;
    --card-black: #0c0d0f;
    --card-gold: #ffb400;
    --gold-text: #f2b31b;
    --tagline-grey: #8a8a8a;
    --white: #ffffff;
    --faint-shade: rgba(120, 70, 0, 0.07);
  }
  * { box-sizing: border-box; margin: 0; padding: 0; }
  html, body { width: 1200px; height: 900px; overflow: hidden; }
  body {
    position: relative;
    background: linear-gradient(to bottom, var(--backdrop-top), var(--backdrop-bottom));
  }
  .card {
    position: absolute;
    top: 184px;
    height: 491px;
    border-radius: 12px;
    overflow: hidden;
    text-align: center;
  }
  .card--front { left: 299px; width: 301px; background: var(--card-black); }
  .card--back { left: 645px; width: 305px; background: var(--card-gold); }

  .brand-square {
    position: absolute;
    left: 50%;
    top: 52px;
    width: 40px;
    height: 40px;
    margin-left: -20px;
    background: var(--card-gold);
  }
  .wordmark {
    position: absolute;
    left: 0; right: 0;
    font-family: "Cinzel", serif;
    font-weight: 400;
    font-size: 23px;
    letter-spacing: 0.3px;
    white-space: nowrap;
  }
  .tagline {
    position: absolute;
    left: 0; right: 0;
    font-family: "Quicksand", sans-serif;
    font-size: 12.5px;
    white-space: nowrap;
  }
  .card--front .wordmark { top: 109px; color: var(--gold-text); }
  .card--front .tagline { top: 137px; color: var(--tagline-grey); }

  .person-name {
    position: absolute;
    left: 0; right: 0;
    top: 360px;
    font-family: "Open Sans", sans-serif;
    font-weight: 700;
    font-size: 16px;
    color: var(--gold-text);
  }
  .contact {
    position: absolute;
    left: 0; right: 0;
    top: 416px;
    font-family: "Open Sans", sans-serif;
    font-size: 13.5px;
    line-height: 18px;
    color: var(--white);
  }

  .faint-band {
    position: absolute;
    left: 0; right: 0; top: 0;
    height: 119px;
    background: var(--faint-shade);
  }
  .faint-square {
    position: absolute;
    left: 56px;
    top: 206px;
    width: 120px;
    height: 120px;
    background: var(--faint-shade);
  }
  .card--back .wordmark { top: 401px; color: var(--white); }
  .card--back .tagline { top: 429px; color: var(--white); }
</style>
</head>
<body>
  <section class="card card--front" aria-label="Business card front">
    <div class="brand-square"></div>
    <p class="wordmark">The Quiet Harbor</p>
    <p class="tagline">staging &amp; design</p>
    <p class="person-name">DANIEL BROOKS</p>
    <p class="contact">555-014-2277<br>hello@quietharbor.example</p>
  </section>

  <section class="card card--back" aria-label="Business card back">
    <div class="faint-band"></div>
    <div class="faint-square"></div>
    <p class="wordmark">The Quiet Harbor</p>
    <p class="tagline">staging &amp; design</p>
  </section>
</body>
</html>
```